Foot and ankle surgeon requires a website design

I need a website where prospective and established patients can obtain information and then direct them to making appointments. My practice is a highly professional surgical practice specialising in surgery to the foot and ankle. My title is Mr Colin Brasket, Podiatric Foot & Ankle Surgeon. My qualifications are: BSc MSc FACPS
The practice website will require information on: Locations, phone numbers to make appointments, general background on podiatric surgery,
I would like to include information on: my hospital appointments, surgical fellowships held, training programs undertaken, association memberships, publications written, links to useful websites
A page dedicated to common foot conditions would be useful and also a page with referral information including an online registration section that will be sent direct to the receptionist.
Examples of similar websites include:
http://www.dorvelquintaro.com.au/
http://www.haldenfootsurgeon.com.au/
I will provide files on logo, self photos and my personal training history etc.
Also if there is going to be a background theme I personally am associated with surfing and beach activities, it would be great if this was able to be reflected in the design.
Thank you.

```html
<!DOCTYPE html>
<html lang="en">
<head>
<meta charset="utf-8">
<title>Mr Colin Brasket – Podiatric Foot &amp; Ankle Surgeon</title>
<link rel="stylesheet" href="https://fonts.googleapis.com/css2?family=Outfit:wght@300;400;500&display=swap">
<style>
:root{
  --blue:#0b4a86;
  --blue-deep:#0a4580;
  --orange:#ea7a14;
  --text:#4a4a4a;
  --rule:#dcdcdc;
  --card:#f2f2f2;
  --white:#ffffff;
}
*{box-sizing:border-box;margin:0;padding:0}
html,body{width:1024px;height:1200px;overflow:hidden;background:var(--white)}
body{position:relative;font-family:"Outfit",sans-serif;color:var(--text);font-weight:300}
.abs{position:absolute}
.top-strip{left:0;top:0;width:1024px;height:3px;background:var(--orange)}
.brand{left:63px;top:62px;display:flex;align-items:center;gap:10px}
.brand-dot{width:34px;height:34px;border-radius:50%;background:var(--orange)}
.brand-name{color:var(--blue);font-weight:500;font-size:21px;line-height:1.05}
.brand-name small{display:block;font-size:11px}
.call{right:63px;top:53px;text-align:right}
.call-label{font-size:14.5px;color:#444;font-weight:400;letter-spacing:.3px}
.call-phone{font-size:23px;color:var(--orange);font-weight:400;margin-top:1px}
.nav{left:0;top:140px;width:1024px;height:38px;background:var(--blue)}
.nav ul{list-style:none;display:flex;position:absolute;left:63px;top:0;height:38px}
.nav li{color:var(--white);font-size:10.5px;font-weight:400;line-height:38px;padding:0 14.6px;letter-spacing:.2px}
.nav li.active{background:var(--orange)}
.hero{left:63px;top:185px;width:898px;height:309px;background:linear-gradient(135deg,#c9b08a,#b89a73 45%,#d4bd98);border:1px solid #ddd}
.hero-title{left:63px;top:248px;width:416px;height:51px;background:rgba(245,242,236,.88);color:var(--blue);font-size:36px;font-weight:400;line-height:51px;padding-left:24px;letter-spacing:.5px}
.hero-body{left:63px;top:301px;width:393px;height:116px;background:rgba(245,242,236,.88);padding:9px 24px 0}
.hero-body p{font-size:14.5px;color:#222;font-weight:400;line-height:19px}
.btn{background:var(--orange);color:var(--white);font-weight:400;text-align:center}
.hero-btn{position:absolute;left:24px;top:76px;width:119px;height:31px;line-height:31px;font-size:14px}
.dots{left:88px;top:466px;display:flex;gap:5px}
.dots span{width:9px;height:9px;background:#111;border-radius:2px}
.dots span:first-child{background:var(--blue)}
.tagline{left:63px;top:519px;width:690px;font-size:19px;color:var(--blue);line-height:24px;font-weight:300}
.appt-btn{left:754px;top:524px;width:207px;height:45px;line-height:43px;font-size:16px;border-bottom:3px solid #c7620b;letter-spacing:.4px}
.rule{left:63px;width:898px;height:1px;background:var(--rule)}
h2{color:var(--orange);font-weight:300;font-size:20.5px}
.welcome{left:63px;top:609px;width:590px}
.welcome h2{margin-bottom:10px}
.welcome p{font-size:11.5px;line-height:18px;margin-bottom:6px}
.welcome-img{left:677px;top:614px;width:284px;height:165px;background:linear-gradient(120deg,#2a2a2a 0 25%,#e9e6df 25% 55%,#c8b58a 55%)}
.conditions{left:62px;top:822px;width:430px}
.conditions p{font-size:11.5px;line-height:18px;margin:12px 0 6px 1px}
.cond-list{list-style:none;display:grid;grid-template-columns:236px 200px;grid-auto-flow:column;grid-template-rows:repeat(7,23.6px);margin-left:1px}
.cond-list li{font-size:11.5px;color:var(--blue);font-weight:400;display:flex;align-items:center;gap:8px}
.cond-list svg{width:11px;height:11px}
.vdivider{left:512px;top:828px;width:1px;height:230px;background:var(--rule)}
.locations-title{left:534px;top:822px}
.loc{top:861px;height:151px;background:var(--card);padding:11px 13px}
.loc h3{font-size:13.5px;color:var(--blue);font-weight:500;margin-bottom:8px}
.loc p{font-size:11.5px;line-height:18px}
.map-link{top:1024px;font-size:11.5px;color:var(--orange);font-weight:400}
.footer{left:0;top:1088px;width:1024px;height:112px;background:var(--blue-deep)}
.copy{left:112px;top:1127px;color:#e6ecf4;font-size:10px;line-height:18px}
.badge-a{left:518px;top:1119px;width:40px;height:51px;background:#8a1a2c}
.badge-b{left:568px;top:1139px;width:120px;height:10px;background:#e9edf3;border-radius:5px}
.badge-c{left:696px;top:1108px;width:87px;height:72px;background:var(--white)}
.connect{left:842px;top:1105px;color:var(--white);font-size:10px;font-weight:400}
.social{left:843px;top:1130px;display:flex;gap:7px}
.social span{width:25px;height:25px;border-radius:50%;background:#6b8fbd}
</style>
</head>
<body>
<div class="abs top-strip"></div>

<header>
  <div class="abs brand">
    <span class="brand-dot"></span>
    <div class="brand-name">Mr Colin Brasket<small>Podiatric Foot &amp; Ankle Surgeon</small></div>
  </div>
  <div class="abs call">
    <div class="call-label">CALL AND MAKE APPOINTMENT</div>
    <div class="call-phone">08 9412 7760</div>
  </div>
</header>

<nav class="abs nav">
  <ul>
    <li class="active">HOME</li>
    <li>APPOINTMENTS</li>
    <li>SURGICAL FELLOWSHIPS</li>
    <li>TRAINING PROGRAMS</li>
    <li>MEMBERSHIPS</li>
    <li>PUBLICATIONS</li>
    <li>USEFUL WEBSITES</li>
    <li>CONTACT US</li>
  </ul>
</nav>

<section>
  <div class="abs hero" role="img" aria-label="Photo of a toddler's bare feet taking first steps on sand and gravel"></div>
  <div class="abs hero-title">TAKE THE FIRST STEP</div>
  <div class="abs hero-body">
    <p>Lorem ipsum dolor sit amet, consectetur adipisicing eitseo eiusmod tempor incididunt ut labore et dolore magna aliqua.</p>
    <div class="btn hero-btn">CONTACT US</div>
  </div>
  <div class="abs dots"><span></span><span></span><span></span><span></span></div>
</section>

<p class="abs tagline">The Tidewater Foot Health Group strive to provide exceptional service and care to all patients, young and old, to ensure they enjoy a pain free lifestyle.</p>
<div class="abs btn appt-btn">MAKE APPOINTMENTS</div>

<div class="abs rule" style="top:594px"></div>

<section class="abs welcome">
  <h2>Welcome to Our Website</h2>
  <p>For those unfamiliar with our services, we are a team of accredited health professionals dealing with the prevention, diagnosis, treatment and rehabilitation of medical and surgical conditions related to feet, ankles and lower limbs.</p>
  <p>The Tidewater Foot Health Group have practices based throughout regional Western Australia in Geraldton and Kalgoorlie and offer the following services; sports injuries, foot care, foot orthoses and diabetes care.</p>
  <p>Many foot and lower limb problems, if identified early can be prevented, so take the right step and contact the Tidewater Foot Health Group for advice on your foot, ankle, heel or leg pain or sports injury.</p>
</section>
<div class="abs welcome-img" role="img" aria-label="Photo of a clinician in a white coat and blue gloves examining a patient's foot"></div>

<div class="abs rule" style="top:806px"></div>

<section class="abs conditions">
  <h2>Foot Condition</h2>
  <p>Many foot and lower limb problems can be prevented if identified early. These are just some of the foot conditions we can treat...</p>
  <ul class="cond-list">
    <li><svg viewBox="0 0 12 12"><path d="M1 6.5l3.2 3L11 2" fill="none" stroke="#ea7a14" stroke-width="2.2"/></svg>Ankle Sprains</li>
    <li><svg viewBox="0 0 12 12"><path d="M1 6.5l3.2 3L11 2" fill="none" stroke="#ea7a14" stroke-width="2.2"/></svg>Hallux Rigidus</li>
    <li><svg viewBox="0 0 12 12"><path d="M1 6.5l3.2 3L11 2" fill="none" stroke="#ea7a14" stroke-width="2.2"/></svg>Hallux Valgus</li>
    <li><svg viewBox="0 0 12 12"><path d="M1 6.5l3.2 3L11 2" fill="none" stroke="#ea7a14" stroke-width="2.2"/></svg>Hammer Toes</li>
    <li><svg viewBox="0 0 12 12"><path d="M1 6.5l3.2 3L11 2" fill="none" stroke="#ea7a14" stroke-width="2.2"/></svg>Medial Tibial Stress Syndrome</li>
    <li><svg viewBox="0 0 12 12"><path d="M1 6.5l3.2 3L11 2" fill="none" stroke="#ea7a14" stroke-width="2.2"/></svg>Morton's Neuroma</li>
    <li><svg viewBox="0 0 12 12"><path d="M1 6.5l3.2 3L11 2" fill="none" stroke="#ea7a14" stroke-width="2.2"/></svg>Osgood-Schlatters Disease</li>
    <li><svg viewBox="0 0 12 12"><path d="M1 6.5l3.2 3L11 2" fill="none" stroke="#ea7a14" stroke-width="2.2"/></svg>Patellofemoral Pain Syndrome</li>
    <li><svg viewBox="0 0 12 12"><path d="M1 6.5l3.2 3L11 2" fill="none" stroke="#ea7a14" stroke-width="2.2"/></svg>Plantar Fasciopathy</li>
    <li><svg viewBox="0 0 12 12"><path d="M1 6.5l3.2 3L11 2" fill="none" stroke="#ea7a14" stroke-width="2.2"/></svg>Severs Disease</li>
    <li><svg viewBox="0 0 12 12"><path d="M1 6.5l3.2 3L11 2" fill="none" stroke="#ea7a14" stroke-width="2.2"/></svg>Sinus Tarsi Syndrome</li>
    <li><svg viewBox="0 0 12 12"><path d="M1 6.5l3.2 3L11 2" fill="none" stroke="#ea7a14" stroke-width="2.2"/></svg>Tarsal Tunnel Syndrome</li>
    <li><svg viewBox="0 0 12 12"><path d="M1 6.5l3.2 3L11 2" fill="none" stroke="#ea7a14" stroke-width="2.2"/></svg>Diabetes</li>
  </ul>
</section>

<div class="abs vdivider"></div>

<section>
  <h2 class="abs locations-title">Locations</h2>
  <div class="abs loc" style="left:523px;width:131px">
    <h3>Geraldton</h3>
    <p>48 Seaspray Parade, PO BOX 2817, Geraldton WA 6530<br>Ph: 08 9412 7760<br>Fax: 08 9412 7761</p>
  </div>
  <div class="abs loc" style="left:665px;width:154px">
    <h3>West End, Geraldton</h3>
    <p>7A &amp; 7B Harbourline Street, Geraldton 6530.<br>Ph: 9412 5530<br>Fax: 9412 5531</p>
  </div>
  <div class="abs loc" style="left:832px;width:129px">
    <h3>Kalgoorlie</h3>
    <p>3/14 Saltbush St, Kalgoorlie WA 6430<br>Ph: 08 9087 2256<br>Fax: 08 9087 2257</p>
  </div>
  <span class="abs map-link" style="left:524px">View Map ››</span>
  <span class="abs map-link" style="left:666px">View Map ››</span>
  <span class="abs map-link" style="left:832px">View Map ››</span>
</section>

<footer class="abs footer"></footer>
<div class="abs copy">Copyright © 2014. CompanyName.<br>All Right Reserved</div>
<div class="abs badge-a" role="img" aria-label="Accreditation badge"></div>
<div class="abs badge-b" role="img" aria-label="Payment partner badge"></div>
<div class="abs badge-c" role="img" aria-label="Charity sponsor badge"></div>
<div class="abs connect">CONNECT US</div>
<div class="abs social" aria-label="Social links">
  <span></span><span></span><span></span><span style="background:var(--orange)"></span>
</div>
</body>
</html>
```